Young, dynamic furniture company needs a new business card design

We require a new business card design for our modern furniture company which supplies furniture and appliances to the property and development market.
Oakridge Interiors has become one of the leading furniture & appliance suppliers to the property market withing London. With over 10 years experience, we have increased our business to supply not only private landlords and managing agents, but also property developers, housing associations and local councils.
We offer not only a complete range of furniture which includes beds, wardrobes, dining sets and sofas, but also a high quality, full delivery and assembly service to help you with all our furnishing needs.

Target Market(s)

Private landlords, estate agents, letting agents, property management companies

Industry/Entity Type

Business

Contact Information for Business Card

Name,
Title,
Address,
Mobile,
Telephone,
Fax, Website, email address

Font styles to use
Sans Serif

Colors
3176b5
0555a3
85abd2
cfdeed

Requirements
Must have
• All the above information for each of our staff, along with our logo

```html
<!DOCTYPE html>
<html lang="en">
<head>
<meta charset="utf-8">
<title>Oakridge Interiors – Business Card</title>
<link rel="stylesheet" href="https://fonts.googleapis.com/css2?family=Roboto:wght@400;500&display=swap">
<style>
  :root {
    --page-bg: #dcd8d2;
    --card-bg: #eef2f6;
    --navy: #1c2f6e;
    --blue-deep: #0555a3;
    --blue: #3176b5;
    --blue-soft: #85abd2;
    --blue-mist: #cfdeed;
    --ink: #1f2530;
    --ink-soft: #2b3340;
    --divider: #9aa3ad;
  }
  * { margin: 0; padding: 0; box-sizing: border-box; }
  html, body {
    width: 1200px; height: 969px; overflow: hidden;
    background: var(--page-bg);
    font-family: "Roboto", Arial, sans-serif;
  }
  .business-card {
    position: absolute; left: 100px; top: 200px;
    width: 1000px; height: 570px;
    background: var(--card-bg);
    overflow: hidden;
    box-shadow: 0 10px 30px rgba(0,0,0,0.18);
  }
  .card-bands { position: absolute; inset: 0; }
  .divider {
    position: absolute; left: 527px; top: 105px;
    width: 2px; height: 310px; background: var(--divider);
  }
  .brand {
    position: absolute; left: 60px; width: 440px; top: 170px;
    text-align: center;
  }
  .brand-square {
    width: 96px; height: 96px; margin: 0 auto 40px;
    background: var(--navy);
  }
  .brand-name {
    font-size: 35px; font-weight: 500; color: var(--ink-soft);
    letter-spacing: 0.5px; text-transform: uppercase; line-height: 1;
  }
  .brand-tagline {
    margin-top: 10px;
    font-size: 17px; font-weight: 500; color: var(--blue-deep);
    letter-spacing: 0.5px; text-transform: uppercase;
  }
  .contact { position: absolute; left: 580px; top: 103px; color: var(--ink); }
  .person-name {
    font-size: 31px; font-weight: 500; color: var(--navy);
    letter-spacing: 0.5px; text-transform: uppercase; line-height: 1.1;
  }
  .person-title {
    font-size: 26px; color: var(--blue-deep);
    text-transform: uppercase; line-height: 1.3;
  }
  .address { margin-top: 14px; font-size: 26px; line-height: 36px; }
  .contact-list { list-style: none; margin-top: 12px; }
  .contact-list li {
    display: flex; align-items: center;
    font-size: 26px; line-height: 38px;
  }
  .contact-list svg { width: 22px; height: 22px; margin: 0 22px 0 6px; fill: var(--ink); flex: none; }
</style>
</head>
<body>
  <div class="business-card">
    <svg class="card-bands" viewBox="0 0 1000 570" width="1000" height="570" aria-hidden="true">
      <defs>
        <linearGradient id="band-top" x1="0" y1="0" x2="1" y2="0">
          <stop offset="0" stop-color="#0555a3"/>
          <stop offset="1" stop-color="#1c2f6e"/>
        </linearGradient>
        <linearGradient id="band-bottom" x1="0" y1="0" x2="1" y2="0">
          <stop offset="0" stop-color="#1c2f6e"/>
          <stop offset="0.6" stop-color="#0555a3"/>
          <stop offset="1" stop-color="#3176b5"/>
        </linearGradient>
      </defs>
      <polygon points="90,0 1000,0 1000,62" fill="var(--blue-soft)" opacity="0.55"/>
      <polygon points="90,0 1000,0 1000,48 480,8" fill="url(#band-top)"/>
      <polygon points="0,488 1000,570 0,570" fill="var(--blue-soft)" opacity="0.55"/>
      <polygon points="0,505 900,570 0,570" fill="url(#band-bottom)"/>
    </svg>

    <div class="divider"></div>

    <div class="brand">
      <div class="brand-square"></div>
      <div class="brand-name">Oakridge Interiors</div>
      <div class="brand-tagline">Trade Furniture Solutions</div>
    </div>

    <div class="contact">
      <div class="person-name">Daniel Marsh</div>
      <div class="person-title">President</div>
      <div class="address">2417 Harrow Lane<br>Millbrook, NY 12545</div>
      <ul class="contact-list">
        <li>
          <svg viewBox="0 0 24 24"><path d="M3 8c0-3 4-5 9-5s9 2 9 5v2h-5V8H8v2H3zM6 11h12l3 9H3z"/></svg>
          555 0142 7781
        </li>
        <li>
          <svg viewBox="0 0 24 24"><path d="M7 1h10a2 2 0 0 1 2 2v18a2 2 0 0 1-2 2H7a2 2 0 0 1-2-2V3a2 2 0 0 1 2-2zm0 3v14h10V4zm5 15.5a1.2 1.2 0 1 0 0 2.4 1.2 1.2 0 0 0 0-2.4z"/></svg>
          555 0199 3046
        </li>
        <li>
          <svg viewBox="0 0 24 24"><path d="M6 2h12v6H6zM2 9h20v9h-4v4H6v-4H2zm6 7v4h8v-4z"/></svg>
          555 0173 6210
        </li>
        <li>
          <svg viewBox="0 0 24 24"><path d="M2 5h20v14H2zm2 2v1l8 5 8-5V7l-8 5z"/></svg>
          daniel@oakridge.example
        </li>
        <li>
          <svg viewBox="0 0 24 24"><path d="M12 2a10 10 0 1 0 0 20 10 10 0 0 0 0-20zm-1 3c-2 1-4 3-3 5 1 1 3 0 3 2s-2 2-2 4 2 3 3 3c-4 0-7-3-7-7a7 7 0 0 1 6-7zm3 1c2 1 4 3 4 6h-3c-1-2 0-3-1-4z"/></svg>
          www.oakridge.example
        </li>
      </ul>
    </div>
  </div>
</body>
</html>
```